Corvane Holdings , new business card design

investment firm with corporate clients . need double sided business card , vertical and horizontal options ,logo must be clear. prefer pantone colors only and sharp design. website also www.corvane.ae

Khalid Bin Tarrafi
Managing Director
Tel. +971 4 387 2940
Mobile +971 50 518 2403
khalid@corvane.ae
Q-Span Plaza, officw 18-B07, Warqa Gardens, Dubai

Contact Information for Business Card

Khalid Bin Tarrafi
Managing Director

Font styles to use
Serif

Colors

Designer to choose colors to be used in the design.

```html
<!DOCTYPE html>
<html lang="en">
<head>
<meta charset="utf-8">
<title>Corvane Holdings — Business Card</title>
<link rel="stylesheet" href="https://fonts.googleapis.com/css2?family=Open+Sans:wght@300;400;700&display=swap">
<style>
  :root {
    --brand-blue: #4a72a0;
    --brand-blue-dark: #3d6190;
    --brand-blue-soft: #5a80ab;
    --ink: #2b2b2b;
    --paper: #ffffff;
    --backdrop: #e9ebee;
    --rule: #d6d9de;
  }
  * { box-sizing: border-box; margin: 0; padding: 0; }
  html, body { width: 1200px; height: 900px; overflow: hidden; }
  body {
    background: var(--backdrop);
    font-family: "Open Sans", Arial, sans-serif;
    position: relative;
  }
  .card {
    position: absolute;
    width: 700px;
    height: 400px;
    border-radius: 22px;
    overflow: hidden;
    box-shadow: 0 6px 18px rgba(0,0,0,0.12);
  }
  /* Front */
  .card-front {
    left: 160px; top: 36px;
    background: var(--paper);
  }
  .card-front .bottom-band {
    position: absolute; left: 0; right: 0; bottom: 0;
    height: 24px; background: var(--brand-blue);
  }
  .card-front .divider {
    position: absolute; left: 348px; top: 70px;
    width: 1px; height: 230px; background: var(--rule);
  }
  .wordmark {
    position: absolute;
    font-weight: 300;
    text-transform: uppercase;
    white-space: nowrap;
  }
  .card-front .wordmark {
    left: 46px; top: 170px;
    font-size: 23px; letter-spacing: 5px;
    color: var(--ink);
  }
  .contact {
    position: absolute; left: 380px; top: 78px;
    color: var(--ink);
  }
  .contact .name {
    font-weight: 700; font-size: 22px; color: var(--brand-blue);
    line-height: 1.2;
  }
  .contact .role { font-size: 15px; margin-bottom: 12px; }
  .contact .address { font-size: 15px; line-height: 1.35; margin-bottom: 12px; }
  .contact .line {
    display: flex; align-items: center; gap: 9px;
    font-size: 16px; line-height: 1.45;
  }
  .contact .line svg { width: 13px; height: 13px; flex: none; }

  /* Back */
  .card-back {
    left: 340px; top: 464px;
    background: var(--brand-blue);
  }
  .card-back .map-area {
    position: absolute; left: 60px; top: 50px;
    width: 580px; height: 300px;
    border-radius: 40px;
    background: radial-gradient(ellipse at center, var(--brand-blue-soft) 0%, var(--brand-blue) 72%);
  }
  .card-back .wordmark {
    left: 0; right: 0; top: 180px;
    text-align: center;
    font-size: 30px; letter-spacing: 8px;
    color: var(--paper);
  }
</style>
</head>
<body>
  <section class="card card-front" aria-label="Business card front">
    <div class="wordmark">Corvane Holdings</div>
    <div class="divider"></div>
    <div class="contact">
      <p class="name">Khalid Bin Tarrafi</p>
      <p class="role">Managing Director</p>
      <p class="address">Q-Span Plaza, officw 18-B07,<br>Warqa Gardens, Dubai</p>
      <p class="line">
        <svg viewBox="0 0 16 16" aria-hidden="true"><path fill="var(--brand-blue)" d="M3 1l3 3-2 2c1 2 3 4 5 5l2-2 3 3-2 2C7 14 2 9 1 3z"/></svg>
        +971 4 387 2940
      </p>
      <p class="line">
        <svg viewBox="0 0 16 16" aria-hidden="true"><rect x="4" y="1" width="8" height="14" rx="1.5" fill="none" stroke="var(--brand-blue)" stroke-width="1.6"/><circle cx="8" cy="12.5" r="0.9" fill="var(--brand-blue)"/></svg>
        +971 50 518 2403
      </p>
      <p class="line">
        <svg viewBox="0 0 16 16" aria-hidden="true"><rect x="1" y="3" width="14" height="10" rx="1" fill="var(--brand-blue)"/><path d="M1.5 3.5L8 9l6.5-5.5" fill="none" stroke="#fff" stroke-width="1.3"/></svg>
        khalid@corvane.ae
      </p>
    </div>
    <div class="bottom-band"></div>
  </section>

  <section class="card card-back" aria-label="Business card back">
    <div class="map-area" role="img" aria-label="Faint dotted world map pattern in lighter blue"></div>
    <div class="wordmark">Corvane Holdings</div>
  </section>
</body>
</html>
```